Business Card Update, need to bring life to the card, two sided color

We need a new business card design, are moving and changing addresses and need a new look, we have the logos already attached but need a new style moving forward. Can incorporate the color of the logo (The Green) as well, maybe a solid back? We deal with safety products revolving around static electricity and safety lighting. Would like to keep same font in second logo as well.

Target Market(s)

Electrical Safety, Lighting

Contact Information for Business Card

Dale Fenwick
Vice President
Office: 770-555-4821
Cell: 770-555-3067
dale@tkfenwick.example
www.tkfenwick.example
4700 West Harbor Boulevard
Suite #150
Roswell, GA 30076

Font styles to use
Serif
Sans Serif

Requirements
Must have
• Since 1918
Nice to have
• Could use the 100 Year Logo for back of card, would like the back of card to be the same green as logo.
Should not have
• No black cards please.

```html
<!DOCTYPE html>
<html lang="en">
<head>
<meta charset="utf-8">
<title>T.K. Fenwick Business Cards</title>
<link rel="stylesheet" href="https://fonts.googleapis.com/css2?family=Arimo:wght@400;700&display=swap">
<style>
  :root {
    --brand-green: #069a5c;
    --band-gray: #8a8a8a;
    --card-white: #ffffff;
    --backdrop: #2d2d2d;
    --text-light: #ffffff;
  }
  * { box-sizing: border-box; margin: 0; padding: 0; }
  html, body { width: 1200px; height: 880px; overflow: hidden; }
  body {
    background: var(--backdrop);
    font-family: "Arimo", Arial, sans-serif;
    position: relative;
  }
  .card {
    position: absolute;
    width: 620px;
    height: 354px;
    border-radius: 18px;
    background: var(--card-white);
    overflow: hidden;
    box-shadow: 0 10px 30px rgba(0,0,0,.45);
  }
  .card-logo-side { left: 110px; top: 60px; background: var(--brand-green); }
  .card-contact-side { left: 470px; top: 466px; }

  .brand-lockup {
    position: absolute;
    display: flex;
    align-items: center;
    gap: 16px;
    color: var(--brand-green);
    font-weight: 700;
  }
  .brand-mark {
    width: 78px; height: 78px;
    border-radius: 50%;
    background: var(--brand-green);
    flex: none;
  }
  .brand-name { line-height: 1.05; }
  .brand-name .primary { display: block; font-size: 34px; letter-spacing: .2px; }
  .brand-name .secondary { display: block; font-size: 16px; margin-top: 4px; }
  .brand-name .since { display: block; font-size: 14px; margin-top: 6px; letter-spacing: 1px; }

  .card-logo-side .brand-lockup { left: 90px; top: 130px; color: var(--text-light); }
  .card-logo-side .brand-mark { background: var(--card-white); }
  .card-contact-side .brand-lockup { left: 40px; top: 46px; }

  .back-bands { position: absolute; inset: 0; }

  .person {
    position: absolute;
    left: 40px; top: 204px;
    color: var(--text-light);
  }
  .person .name { font-size: 19px; font-weight: 700; letter-spacing: .5px; }
  .person .role { font-size: 15px; margin-top: 3px; }

  .contact-list {
    position: absolute;
    left: 40px; top: 266px;
    list-style: none;
    color: var(--text-light);
    font-size: 14px;
  }
  .contact-list li { display: flex; align-items: center; gap: 10px; height: 19px; }
  .contact-list .label { width: 44px; }
  .contact-list svg { width: 15px; height: 15px; flex: none; }

  .address {
    position: absolute;
    right: 30px; top: 232px;
    text-align: right;
    color: var(--text-light);
    font-size: 15px;
    line-height: 1.35;
  }
</style>
</head>
<body>

  <section class="card card-logo-side" aria-label="Card logo side">
    <div class="brand-lockup">
      <span class="brand-mark"></span>
      <span class="brand-name">
        <span class="primary">T.K. Fenwick</span>
        <span class="secondary">Manufacturing Company, Inc.</span>
        <span class="since">SINCE 1918</span>
      </span>
    </div>
  </section>

  <section class="card card-contact-side" aria-label="Card contact side">
    <svg class="back-bands" width="620" height="354" viewBox="0 0 620 354" aria-hidden="true">
      <rect x="0" y="190" width="620" height="164" fill="var(--band-gray)"/>
      <path d="M0 258 H285 Q300 258 300 242 V222 Q300 206 316 206 H620 V354 H0 Z" fill="var(--brand-green)"/>
    </svg>

    <div class="brand-lockup">
      <span class="brand-mark"></span>
      <span class="brand-name">
        <span class="primary">T.K. Fenwick</span>
        <span class="secondary">Manufacturing Company, Inc.</span>
        <span class="since">SINCE 1918</span>
      </span>
    </div>

    <div class="person">
      <div class="name">DALE FENWICK</div>
      <div class="role">Vice President</div>
    </div>

    <ul class="contact-list">
      <li>
        <svg viewBox="0 0 16 16"><circle cx="8" cy="8" r="7" fill="none" stroke="#fff" stroke-width="1.3"/><path d="M5.5 4.5l1.5 1.5-1 1a5 5 0 0 0 3 3l1-1 1.5 1.5-1 1c-3 0-6-3-6-6z" fill="#fff"/></svg>
        <span class="label">Office</span>770-555-4821
      </li>
      <li>
        <svg viewBox="0 0 16 16"><circle cx="8" cy="8" r="7" fill="none" stroke="#fff" stroke-width="1.3"/><rect x="5.5" y="3.8" width="5" height="8.4" rx="1" fill="none" stroke="#fff"/><circle cx="8" cy="10.5" r=".7" fill="#fff"/></svg>
        <span class="label">Cell</span>770-555-3067
      </li>
      <li>
        <svg viewBox="0 0 16 16"><circle cx="8" cy="8" r="7" fill="none" stroke="#fff" stroke-width="1.3"/><rect x="4.5" y="5.5" width="7" height="5" fill="none" stroke="#fff"/><path d="M4.5 5.5L8 8.3 11.5 5.5" fill="none" stroke="#fff"/></svg>
        dale@tkfenwick.example
      </li>
      <li>
        <svg viewBox="0 0 16 16"><circle cx="8" cy="8" r="7" fill="none" stroke="#fff" stroke-width="1.3"/><circle cx="8" cy="8" r="3.8" fill="none" stroke="#fff"/><path d="M4.2 8h7.6M8 4.2v7.6" stroke="#fff"/></svg>
        www.tkfenwick.example
      </li>
    </ul>

    <div class="address">
      4700 West Harbor Boulevard<br>
      Suite #150<br>
      Roswell, GA 30076
    </div>
  </section>

</body>
</html>
```